Indian Wedding Flick Post Geofilter

I need a flick post filter design for my cousins wedding. I need a picture of a bear in the top left corner and ostrich in the bottom right corner. I need the words Marcus Weds Dilip on it as well. Also a nice border may be nice.
** web-optimized, transparent PNG.
*** PNG should have a width of 1080 pixels and a height of 1920 pixels
**** PNG must be under 300KB.

Industry/Entity Type

Wedding

Number of Pages Required

1 page

Font styles to use
Decorative

Colors
85acd3
3277b5
296eb1
eea4c8
e667a6

```html
<!DOCTYPE html>
<html lang="en">
<head>
<meta charset="utf-8">
<title>Marcus Weds Dilip – Wedding Geofilter</title>
<link rel="stylesheet" href="https://fonts.googleapis.com/css2?family=Alfa+Slab+One&family=Roboto+Slab:wght@800&display=swap">
<style>
  :root {
    --groom-blue: #296eb1;
    --groom-frame: #3277b5;
    --bride-pink: #e667a6;
    --bride-frame: #e667a6;
    --card-white: #ffffff;
    --heart-red: #b0101a;
    --heart-dark: #7d0a10;
    --bear-tone: #3d3c48;
    --ostrich-tone: #7a4a22;
    --ring-gold: #e2a93a;
  }
  html, body {
    margin: 0;
    padding: 0;
    overflow: hidden;
  }
  body {
    width: 675px;
    height: 1200px;
  }
  .filter-canvas {
    position: relative;
    width: 675px;
    height: 1200px;
    background: #ffffff;
    overflow: hidden;
  }
  .bear-illustration {
    position: absolute;
    left: 18px;
    top: 48px;
    width: 362px;
    height: 210px;
    border-radius: 40% 45% 20% 20%;
    background: linear-gradient(180deg, #45444f 0%, var(--bear-tone) 60%, #2a2a33 100%);
  }
  .ostrich-illustration {
    position: absolute;
    left: 350px;
    top: 724px;
    width: 303px;
    height: 440px;
    border-radius: 30% 50% 20% 20%;
    background: linear-gradient(180deg, #c9b29a 0%, #8b5a2b 45%, var(--ostrich-tone) 70%, #a57a55 100%);
  }
  .name-card {
    position: absolute;
    box-sizing: border-box;
    background: var(--card-white);
    display: flex;
    align-items: center;
    box-shadow: 4px 6px 8px rgba(0,0,0,0.35);
  }
  .name-card--groom {
    left: 50px;
    top: 322px;
    width: 566px;
    height: 150px;
    border: 10px solid var(--groom-frame);
    transform: rotate(-8deg);
    padding-left: 62px;
  }
  .name-card--bride {
    left: 66px;
    top: 524px;
    width: 566px;
    height: 158px;
    border: 10px solid var(--bride-frame);
    transform: rotate(9deg);
    padding-left: 80px;
  }
  .name-card__name {
    font-family: "Alfa Slab One", serif;
    font-size: 88px;
    line-height: 1;
    letter-spacing: 1px;
    white-space: nowrap;
    text-shadow:
      -3px -3px 0 #fff, 3px -3px 0 #fff, -3px 3px 0 #fff, 3px 3px 0 #fff,
      5px 6px 4px rgba(0,0,0,0.35);
  }
  .name-card--groom .name-card__name { color: var(--groom-blue); }
  .name-card--bride .name-card__name { color: var(--bride-pink); }
  .ring-ornament {
    position: absolute;
    right: 14px;
    bottom: 14px;
    width: 54px;
    height: 48px;
    border-radius: 50%;
    background: radial-gradient(circle at 40% 40%, #f7d27a 0%, var(--ring-gold) 60%, #b77b1c 100%);
  }
  .weds-heart {
    position: absolute;
    left: 508px;
    top: 448px;
    width: 118px;
    height: 86px;
  }
  .weds-heart__label {
    font-family: "Roboto Slab", serif;
    font-weight: 800;
    font-size: 15px;
    fill: #ffffff;
  }
</style>
</head>
<body>
  <main class="filter-canvas">
    <div class="bear-illustration" role="img" aria-label="Illustration of a black bear walking, facing left"></div>

    <div class="name-card name-card--groom">
      <span class="name-card__name">Marcus</span>
      <div class="ring-ornament" role="img" aria-label="Gold wedding ring with red heart gem"></div>
    </div>

    <div class="name-card name-card--bride">
      <span class="name-card__name">Dilip</span>
      <div class="ring-ornament" role="img" aria-label="Gold wedding ring with red heart gem"></div>
    </div>

    <svg class="weds-heart" viewBox="0 0 118 86" role="img" aria-label="Weds">
      <path d="M40 84 C10 60 0 46 0 30 C0 14 12 4 24 4 C33 4 39 10 42 16 C45 10 51 4 60 4 C72 4 80 14 80 30 C80 46 70 60 40 84 Z" fill="var(--heart-dark)"/>
      <path d="M74 82 C44 58 34 44 34 28 C34 12 46 2 58 2 C67 2 73 8 76 14 C79 8 85 2 94 2 C106 2 118 12 118 28 C118 44 104 58 74 82 Z" fill="var(--heart-red)" stroke="#f2d6d6" stroke-width="1.5" stroke-dasharray="2 2"/>
      <text class="weds-heart__label" x="76" y="43" text-anchor="middle">Weds</text>
    </svg>

    <div class="ostrich-illustration" role="img" aria-label="Illustration of a standing ostrich facing left"></div>
  </main>
</body>
</html>
```